Bluecrest Learning Corps by graduating students from college in two years

Based on the logo design, create stationary and business cards for
Dr. Venrel T Oskamp, CEO, (703) 482-1736
and Marisa Deltoft, Respresentative, (301) 647-2208
Address: 4719 Pellham Court, Ashmere Falls, VA 20417
Incorporate elelments of the logo

Target Market(s)

USA

Font styles to use
Other font styles liked:
• match with the logo type style

```html
<!DOCTYPE html>
<html lang="en">
<head>
<meta charset="utf-8">
<title>Bluecrest Learning Corps – Stationery</title>
<link href="https://fonts.googleapis.com/css2?family=Tinos:ital,wght@0,400;0,700;1,700&family=Roboto+Condensed:wght@400;700&family=Playfair+Display:ital,wght@1,700&display=swap" rel="stylesheet">
<style>
  :root{
    --navy:#1d285a;
    --navy-soft:#273366;
    --gold:#fdc42d;
    --paper:#ffffff;
    --ink:#1a1a1a;
    --stage:#d3d9dd;
    --stage-light:#e3e7ea;
  }
  *{box-sizing:border-box;margin:0;padding:0}
  html,body{width:1200px;height:916px;overflow:hidden}
  body{
    position:relative;
    background:radial-gradient(ellipse at 50% 40%,var(--stage-light),var(--stage));
    font-family:"Tinos",serif;
  }
  .card{
    position:absolute;left:70px;width:436px;height:250px;
    background:var(--navy);
    border-radius:27px;
    border-bottom:4px solid var(--gold);
    overflow:hidden;
    box-shadow:0 6px 14px rgba(0,0,0,.28);
  }
  .card--front{top:65px;display:flex;align-items:center;justify-content:center;gap:12px;background:var(--navy-soft)}
  .card--rep{top:339px}
  .card--ceo{top:613px}
  .brand-dot{width:22px;height:22px;border-radius:50%;background:var(--gold);flex:none}
  .brand-name{font-family:"Tinos",serif;font-weight:700;color:var(--gold);font-size:24px;letter-spacing:.5px}
  .card .brand{position:absolute;left:38px;top:104px;width:150px;display:flex;flex-direction:column;align-items:center;gap:8px;text-align:center}
  .card .brand .brand-name{font-size:17px;line-height:1.15}
  .divider{position:absolute;left:216px;top:45px;width:2px;height:158px;background:var(--gold)}
  .details{position:absolute;left:247px;right:8px;top:60px;color:#fff}
  .person{font-weight:700;color:var(--gold);font-size:18px;line-height:24px;letter-spacing:.2px;white-space:nowrap}
  .role{font-size:11.5px;line-height:13px}
  .address{margin-top:9px;font-size:11.5px;line-height:15px;white-space:nowrap}
  .contacts{margin-top:9px;list-style:none;font-size:11.5px;line-height:15px}
  .contacts li{display:flex;align-items:center;gap:6px;white-space:nowrap}
  .contacts svg{width:10px;height:10px;flex:none;color:var(--gold)}
  .band{position:absolute;left:0;right:0;top:220px;height:16px;display:flex}
  .band .gold{width:213px;background:var(--gold)}
  .band .white{flex:1;background:#fff}

  .letterhead{
    position:absolute;left:563px;top:65px;width:558px;height:787px;
    background:var(--paper);
    box-shadow:0 6px 18px rgba(0,0,0,.25);
    color:var(--ink);
  }
  .lh-brand{position:absolute;left:29px;top:54px;display:flex;align-items:center;gap:8px}
  .lh-brand .brand-dot{width:16px;height:16px}
  .lh-brand .brand-name{color:var(--navy);font-size:16px}
  .lh-contact{position:absolute;right:28px;top:36px;list-style:none;text-align:right;color:var(--navy);font-size:10.5px;line-height:15px}
  .lh-contact li{display:flex;justify-content:flex-end;align-items:center;gap:5px;white-space:nowrap}
  .lh-contact svg{width:9px;height:9px;color:var(--gold)}
  .rule{position:absolute;left:29px;top:116px;width:500px;height:3px}
  .rule .navy-line{position:absolute;left:0;top:1px;width:319px;height:1px;background:var(--navy)}
  .rule .gold-line{position:absolute;left:319px;top:0;width:181px;height:3px;background:var(--gold)}
  .sender{position:absolute;left:29px;top:176px}
  .split-name{font-family:"Roboto Condensed",sans-serif;font-size:27px;line-height:30px;color:var(--navy)}
  .split-name b{color:var(--gold);font-weight:700}
  .title{font-size:10.5px;line-height:13px;margin-left:1px}
  .date{position:absolute;right:44px;top:185px;font-size:12.5px}
  .sender-contact{position:absolute;left:29px;top:233px;list-style:none;font-size:10px;line-height:13.5px}
  .sender-contact li{display:flex;align-items:center;gap:6px}
  .sender-contact svg{width:8px;height:8px;color:var(--gold)}
  .body{position:absolute;left:28px;top:294px;width:498px;font-size:11.2px;line-height:15.8px;text-align:justify}
  .body p+p{margin-top:15px}
  .signature{position:absolute;left:29px;top:568px;width:188px;height:58px;background:linear-gradient(90deg,#f3f3f5,#e6e6ea)}
  .signer{position:absolute;left:28px;top:633px}
  .footer-band{position:absolute;left:0;right:0;top:748px;height:14px;display:flex}
  .footer-band .gold{width:280px;background:var(--gold)}
  .footer-band .navy{flex:1;background:var(--navy)}

  .caption{
    position:absolute;font-family:"Playfair Display",serif;font-style:italic;font-weight:700;
    color:#fff;font-size:32px;text-shadow:0 2px 4px rgba(0,0,0,.35);
  }
  .caption--cards{left:145px;top:866px}
  .caption--letter{left:728px;top:858px;font-size:34px}
</style>
</head>
<body>
<svg width="0" height="0" style="position:absolute">
  <defs>
    <symbol id="i-phone" viewBox="0 0 10 10"><path d="M2 .5l2 2-1 1.2c.6 1.3 1.5 2.2 2.8 2.8L7 5.5l2 2-1 1.7C4.5 9 1 5.5.8 2z" fill="currentColor"/></symbol>
    <symbol id="i-globe" viewBox="0 0 10 10"><circle cx="5" cy="5" r="4.3" fill="none" stroke="currentColor" stroke-width="1.1"/><path d="M.7 5h8.6M5 .7c-2.2 2.6-2.2 6 0 8.6M5 .7c2.2 2.6 2.2 6 0 8.6" fill="none" stroke="currentColor" stroke-width=".8"/></symbol>
    <symbol id="i-mail" viewBox="0 0 10 10"><rect x=".6" y="2" width="8.8" height="6.2" fill="none" stroke="currentColor" stroke-width="1.1"/><path d="M.6 2L5 5.6 9.4 2" fill="none" stroke="currentColor" stroke-width="1"/></symbol>
    <symbol id="i-pin" viewBox="0 0 10 10"><path d="M5 9.6S1.6 5.8 1.6 3.6a3.4 3.4 0 016.8 0C8.4 5.8 5 9.6 5 9.6z" fill="none" stroke="currentColor" stroke-width="1.1"/><circle cx="5" cy="3.6" r="1.1" fill="currentColor"/></symbol>
  </defs>
</svg>

<section class="card card--front" aria-label="Business card front">
  <span class="brand-dot"></span>
  <span class="brand-name">Bluecrest Learning Corps</span>
</section>

<section class="card card--rep" aria-label="Business card, representative">
  <div class="brand"><span class="brand-dot"></span><span class="brand-name">Bluecrest Learning Corps</span></div>
  <div class="divider"></div>
  <div class="details">
    <div class="person">Marisa Deltoft</div>
    <div class="role">Respresentative</div>
    <div class="address">4719 Pellham Court,<br>Ashmere Falls, VA 20417</div>
    <ul class="contacts">
      <li><svg><use href="#i-phone"/></svg>(301) 647-2208</li>
      <li><svg><use href="#i-globe"/></svg>www.bluecrestcorps.org</li>
      <li><svg><use href="#i-mail"/></svg>info@bluecrestcorps.org</li>
    </ul>
  </div>
  <div class="band"><span class="gold"></span><span class="white"></span></div>
</section>

<section class="card card--ceo" aria-label="Business card, CEO">
  <div class="brand"><span class="brand-dot"></span><span class="brand-name">Bluecrest Learning Corps</span></div>
  <div class="divider"></div>
  <div class="details">
    <div class="person">Dr. Venrel T Oskamp</div>
    <div class="role">CEO</div>
    <div class="address">4719 Pellham Court,<br>Ashmere Falls, VA 20417</div>
    <ul class="contacts">
      <li><svg><use href="#i-phone"/></svg>(703) 482-1736</li>
      <li><svg><use href="#i-globe"/></svg>www.bluecrestcorps.org</li>
      <li><svg><use href="#i-mail"/></svg>info@bluecrestcorps.org</li>
    </ul>
  </div>
  <div class="band"><span class="gold"></span><span class="white"></span></div>
</section>

<article class="letterhead" aria-label="A4 letterhead">
  <div class="lh-brand"><span class="brand-dot"></span><span class="brand-name">Bluecrest Learning Corps</span></div>
  <ul class="lh-contact">
    <li>(301) 647-2208<svg><use href="#i-phone"/></svg></li>
    <li>www.bluecrestcorps.org<svg><use href="#i-globe"/></svg></li>
    <li>info@bluecrestcorps.org<svg><use href="#i-mail"/></svg></li>
    <li>4719 Pellham Court, Ashmere Falls, VA 20417<svg><use href="#i-pin"/></svg></li>
  </ul>
  <div class="rule"><span class="navy-line"></span><span class="gold-line"></span></div>

  <div class="sender">
    <div class="split-name"><b>Ilvena</b> Marstok</div>
    <div class="title">Founder &amp; CEO</div>
  </div>
  <div class="date">August-05-2019</div>
  <ul class="sender-contact">
    <li><svg><use href="#i-phone"/></svg>(817) 530-4192</li>
    <li><svg><use href="#i-globe"/></svg>www.bluecrestcorps.org</li>
    <li><svg><use href="#i-mail"/></svg>info@bluecrestcorps.org</li>
  </ul>

  <div class="body">
    <p>Lorem ipsum dolor sit amet, consectetuer adipiscing elit, sed diam nonummy nibh euismod tincidunt ut laoreet dolore magna aliquam erat volutpat. Ut wisi enim ad minim veniam, quis nostrud exerci tation ullamcorper suscipit lobortis</p>
    <p>Lorem ipsum dolor sit amet, cons ectetuer adipiscing elit, sed diam nonummy nibh euismod tincidunt ut laoreet dolore magna aliquam erat volutpat. Ut wisi enim ad minim veniam, quis nostrud exerci tation ullamcorper suscipit lobortis nisl ut aliquip ex ea commodo consequat. Lorem ipsum dolor sit amet, consectetuer olutpat. Ut wisi enim ad minim veniam, quis nostrud exerci tation ullamcorper suscipit lobortis nisl ut aliquip ex ea commodo consequat. Duis autem</p>
    <p>vel eum iriure dolor in hendrerit in vulputate velit esse molestie consequat, vel illum dolore eu feugiat nulla facilisis at vero eros et accumsan et iusto odio dignissim qui blandit praesent luptatum zzril delenit augue duis dolore te feugait nulla facilisi. Lorem ipsum dolor sit amet, cons ectetuer adipiscing elit, sed diam nonummy nibh euismod tincidunt ut laoreet dolore magna aliquam erat volutpat. Ut wisi enim .</p>
  </div>

  <div class="signature" role="img" aria-label="Handwritten signature of the director"></div>
  <div class="signer">
    <div class="split-name"><b>Teodra</b> Vaskelin</div>
    <div class="title">Director</div>
  </div>

  <div class="footer-band"><span class="gold"></span><span class="navy"></span></div>
</article>

<div class="caption caption--cards">Business card</div>
<div class="caption caption--letter">A4 Letterhead</div>
</body>
</html>
```